Hollow Thicket, a 3d voxel survival video game needs a card for gaming conventions

I am the lead developer for Hollow Thicket http://www.HollowThicket.example and need a business card to hand out at an indie gaming convention
The card would need to include the game name, website url, my name, position (Lead Developer), e-mail and phone number
The game is a 3d, voxel (with smooth terrain) based survival game with guns and wildlife. The main icon of the game would likely be a grizzly bear but I am willing to accept other designs too.
Attached is a media kit for the game with some images you can use but don't have to its just what little art I can provide. Anything on the website or from the video game can also be used. unrelated art can also be used.
Target Market(s)
Indie Developers/publishers at conferences
Industry/Entity Type
Games
Contact Information for Business Card
Name: Corin Waldrick
Position: Lead Developer
E-mail: Pale_Kettle@mailbox.example
Phone number: 555-372-1186

```html
<!DOCTYPE html>
<html lang="en">
<head>
<meta charset="utf-8">
<title>Hollow Thicket – Business Card</title>
<link rel="stylesheet" href="https://fonts.googleapis.com/css2?family=Rajdhani:wght@600;700&family=Roboto:wght@400&display=swap">
<style>
  :root {
    --backdrop: #a8a5a6;
    --card: #26272b;
    --ink-light: #f1f1f1;
    --ink-soft: #dcdcdc;
    --brand-tan: #b3a77c;
    --band-red: #9c1717;
    --band-tan: #8c876c;
    --art-dark: #2e2620;
    --art-brown: #6e4a30;
  }
  * { box-sizing: border-box; margin: 0; padding: 0; }
  html, body { width: 1200px; height: 1200px; overflow: hidden; }
  body { background: var(--backdrop); position: relative; font-family: "Roboto", sans-serif; }

  .card {
    position: absolute;
    width: 714px;
    height: 421px;
    background: var(--card);
    overflow: hidden;
  }
  .card--front { left: 237px; top: 118px; }
  .card--back  { left: 229px; top: 644px; }

  .mascot-art {
    position: absolute;
    background: radial-gradient(ellipse at 55% 40%, var(--art-brown) 0%, var(--art-dark) 65%, rgba(38,39,43,0) 100%);
    border-radius: 45% 45% 20% 20%;
  }
  .card--front .mascot-art { left: 220px; top: 78px; width: 184px; height: 172px; }
  .card--back  .mascot-art { left: 84px;  top: 92px; width: 124px; height: 116px; }

  .wordmark {
    position: absolute;
    font-family: "Rajdhani", sans-serif;
    font-weight: 700;
    color: var(--brand-tan);
    text-transform: uppercase;
    text-align: center;
    line-height: 0.95;
    letter-spacing: 2px;
  }
  .card--front .wordmark { left: 170px; top: 238px; width: 380px; font-size: 58px; }
  .card--back  .wordmark { left: 50px;  top: 206px; width: 270px; font-size: 41px; }

  .contact { position: absolute; left: 369px; top: 118px; color: var(--ink-light); }
  .contact__name {
    font-family: "Rajdhani", sans-serif;
    font-weight: 700;
    font-size: 28px;
    line-height: 1;
  }
  .contact__role { font-size: 16px; color: var(--ink-soft); margin-top: 8px; }
  .contact__list { list-style: none; margin-top: 30px; }
  .contact__item { display: flex; align-items: center; font-size: 17.5px; height: 26px; }
  .contact__icon { width: 17px; height: 14px; margin-right: 19px; fill: var(--ink-light); }

  .bands { position: absolute; left: 0; bottom: 0; width: 714px; height: 54px; }
  .website {
    position: absolute;
    left: 369px;
    top: 384px;
    font-size: 17px;
    color: var(--ink-light);
  }
</style>
</head>
<body>
  <section class="card card--front">
    <div class="mascot-art" role="img" aria-label="Photo of a roaring grizzly bear"></div>
    <div class="wordmark">Hollow<br>Thicket</div>
  </section>

  <section class="card card--back">
    <div class="mascot-art" role="img" aria-label="Photo of a roaring grizzly bear"></div>
    <div class="wordmark">Hollow<br>Thicket</div>

    <div class="contact">
      <h1 class="contact__name">Corin Waldrick</h1>
      <p class="contact__role">Lead Developer</p>
      <ul class="contact__list">
        <li class="contact__item">
          <svg class="contact__icon" viewBox="0 0 17 14" aria-hidden="true">
            <path d="M1 4 Q8.5 -1 16 4 L14 6 L11.5 4.5 L5.5 4.5 L3 6 Z"/>
            <path d="M4 7 L13 7 L15 13 L2 13 Z"/>
          </svg>555-372-1186
        </li>
        <li class="contact__item">
          <svg class="contact__icon" viewBox="0 0 17 14" aria-hidden="true">
            <path d="M1 2 L16 2 L16 13 L1 13 Z M2 3 L8.5 8.5 L15 3 L15 12 L10.5 7.5 L8.5 9.5 L6.5 7.5 L2 12 Z" fill-rule="evenodd"/>
          </svg>Pale_Kettle@mailbox.example
        </li>
      </ul>
    </div>

    <svg class="bands" viewBox="0 0 714 54" aria-hidden="true">
      <polygon points="0,32 320,32 306,54 0,54" fill="var(--band-tan)"/>
      <polygon points="336,0 714,0 714,54 304,54" fill="var(--band-red)"/>
    </svg>
    <p class="website">www.hollowthicket.example</p>
  </section>
</body>
</html>
```